Under Morning Lantern website

I need a website to sell my t-shirt designs. I have around 5 designs I plan to sell on my initial launch, but only 3 photos at the moment. I would love a main page with the product images below maybe a large nicely designed header image, showing products with their sizes, item name/description, a way to add to cart and a review system like stars below each product image. Maybe a share option to Glimmergram, Friendbook, Chirper, Pinterest, etc. would be cool too. Also on the main page under the product images a section showcasing my Glimmergram photos for the company. Then a section where I will include an About Me video from like YouTube. Lastly, on the main page an option to join my Mailing List at the footer with links to my Friendbook and Glimmergram social accounts, links to pages (About Me, Shop, Glimmergram page, & Contact Us) as well as Track Order.

The other 4 pages will be for an About Me, which is the video I will make later that will be from YouTube. Then the Shop page. Then the Glimmergram page showcasing all the photos I plan to use to market the products, and a Contact Us Page.

I plan to possibly connect this to Shopify, so showcasing payment options (Palo, Birch Pay, Wayfarer, etc.) would be nice.

Lastly, I don't plan on doing returns/exchanges so maybe an area showing that would be nice too. ALL SALES FINAL

Mobile Friendly!

1st image is logo and other 4 images are t-shirt designs

Coded - Design and coding required

5+ page

• Separate pages, No Refunds (All Sales Final), Add to Cart, Way to Purchase

```html
<!DOCTYPE html>
<html lang="en">
<head>
<meta charset="utf-8">
<title>Under Morning Lantern – About Me</title>
<link href="https://fonts.googleapis.com/css2?family=Poppins:wght@400;500;600;700&family=Roboto:wght@400;500;700&display=swap" rel="stylesheet">
<style>
:root{
  --sky:#03abe9;
  --ink:#111;
  --plum:#4a3a6b;
  --white:#fff;
  --grey-panel:#f2f2f2;
  --footer:#2b2b2b;
  --footer-deep:#232323;
  --footer-text:#b5b5b5;
  --footer-line:#444;
  --body-text:#333;
}
*{margin:0;padding:0;box-sizing:border-box}
html,body{width:825px;height:1200px;overflow:hidden;background:var(--white)}
body{position:relative;font-family:"Roboto",sans-serif;color:var(--body-text)}
.abs{position:absolute}

/* header */
.hero{left:0;top:0;width:825px;height:216px;background:var(--sky)}
.brand{left:81px;top:27px;width:125px;text-align:center;color:var(--ink)}
.brand-name{font-family:"Poppins",sans-serif;font-weight:700;font-size:28px;line-height:30px;letter-spacing:1px}
.brand-tag{font-family:"Poppins",sans-serif;font-weight:700;font-size:5.5px;letter-spacing:1.6px;margin-top:1px}
.nav{left:244px;top:30px;width:437px;height:30px;background:var(--white);border-radius:15px;overflow:hidden;display:flex;align-items:center;font-size:11.5px}
.nav a{color:var(--ink);text-decoration:none;position:absolute;top:8px}
.nav .active{color:var(--sky)}
.nav .active::after{content:"";position:absolute;left:50%;bottom:-5px;width:3px;height:3px;margin-left:-1.5px;border-radius:50%;background:var(--sky)}
.nav .track{left:319px;top:0;width:118px;height:30px;background:var(--ink);color:var(--white);display:flex;align-items:center;justify-content:center;border-radius:0 15px 15px 0}
.cart{left:721px;top:33px}
.hero-title{left:0;top:134px;width:825px;text-align:center;font-family:"Poppins",sans-serif;font-weight:600;font-size:24px;color:var(--white)}
.crumbs{left:0;top:170px;width:825px;text-align:center;font-size:10.5px;color:var(--white);word-spacing:2px}
.crumbs span{margin:0 9px}

/* about section */
.section-title{left:0;top:262px;width:825px;text-align:center;font-family:"Poppins",sans-serif;font-weight:600;font-size:24px;color:var(--plum)}
.section-title em{font-style:normal;color:var(--sky)}
.section-rule{left:397px;top:295px;width:31px;height:2px;background:var(--sky)}
.side-panel{top:415px;width:115px;height:112px;background:var(--grey-panel)}
.video{left:132px;top:312px;width:561px;height:316px;overflow:hidden}
.video-frame{position:absolute;inset:0;background:linear-gradient(100deg,#8b7f78 0%,#6a5a78 35%,#4d3a68 55%,#2f5e5c 72%,#6d7a4a 88%,#8c8470 100%)}
.video-caption{position:absolute;left:140px;top:30px;font-family:"Poppins",sans-serif;font-size:17px;color:#e7e4ea}
.play-big{position:absolute;left:258px;top:115px}
.controls{position:absolute;left:0;top:287px;width:561px;height:29px;background:#161616;font-family:"Poppins",sans-serif;font-size:7.5px;color:var(--white)}
.progress{position:absolute;left:29px;top:13px;width:419px;height:3px;background:#3a3a3a}
.progress i{position:absolute;left:0;top:0;width:91px;height:3px;background:#9a9a9a}
.time{position:absolute;left:456px;top:10px}
.hd{position:absolute;left:535px;top:10px;color:var(--sky);font-weight:700}

/* social feed */
.feed-title{left:187px;top:668px;font-family:"Poppins",sans-serif;font-weight:600;font-size:19px;color:#333}
.feed-text{left:187px;top:698px;width:460px;font-family:"Poppins",sans-serif;font-size:10.8px;line-height:14px;color:#333}
.tile{position:absolute}
.tile-feature{left:175px;top:748px;width:219px;height:202px;background:radial-gradient(ellipse at 50% 50%,#6a4c93 0%,#4c3d6a 35%,#383d48 65%)}
.tile-a{left:402px;top:748px;width:123px;height:98px;background:linear-gradient(160deg,#b9cfe0,#6f7a80 60%,#4c5256)}
.tile-b{left:533px;top:748px;width:117px;height:98px;background:linear-gradient(180deg,#e9eaeb,#9f9486 60%,#6a5a45)}
.tile-c{left:402px;top:853px;width:123px;height:97px;background:linear-gradient(135deg,#5d6266,#3f4447 60%,#8e9194)}
.tile-d{left:533px;top:853px;width:117px;height:97px;background:linear-gradient(180deg,#c7d3da,#a0acb2 55%,#7b7f80)}

/* footer */
.footer{left:0;top:999px;width:825px;height:149px;background:var(--footer)}
.footer-bottom{left:0;top:1148px;width:825px;height:52px;background:var(--footer-deep)}
.policy{left:81px;top:1030px;font-size:8.6px;line-height:18px;color:var(--sky)}
.policy-rule{left:80px;top:1073px;width:132px;height:1px;background:var(--footer-line)}
.contact-lines{left:81px;top:1083px;font-size:8.6px;line-height:17px;color:var(--footer-text)}
.divider{top:1033px;width:1px;height:96px;background:var(--footer-line)}
.col-title{font-size:10.5px;color:var(--white)}
.links{left:255px;top:1055px;font-size:8.8px;line-height:15.7px;color:var(--footer-text)}
.news-note{left:359px;top:1048px;font-size:8.8px;color:var(--footer-text)}
.subscribe{left:353px;top:1074px;width:250px;height:25px;border-radius:13px;overflow:hidden;background:#e8eef3;font-size:8.8px}
.subscribe .field{position:absolute;left:18px;top:7px;color:#8a96a0}
.subscribe .btn{position:absolute;left:168px;top:0;width:82px;height:25px;background:var(--sky);color:var(--white);font-weight:700;display:flex;align-items:center;justify-content:center}
.socials{left:359px;top:1111px;display:flex;gap:10px}
.socials i{display:block;width:10px;height:10px;border-radius:50%;background:#9a9a9a}
.brand-foot{left:651px;top:1024px;width:90px;text-align:center;color:var(--sky)}
.brand-foot .brand-name{font-size:20px;line-height:22px}
.brand-foot .brand-tag{font-size:4px;letter-spacing:1.2px;color:var(--white)}
.track-btn{left:655px;top:1073px;width:93px;height:26px;background:#2aa8ea;color:var(--white);font-size:9.5px;display:flex;align-items:center;justify-content:center}
.copyright{left:82px;top:1167px;font-size:9.5px;color:#9a9a9a}
.cards{left:507px;top:1162px;display:flex;gap:7px}
.card{width:34px;height:21px;background:var(--white);border-radius:2px;display:flex;align-items:center;justify-content:center;font-size:5.6px;font-weight:700;color:#333}
</style>
</head>
<body>

<header class="abs hero"></header>
<div class="abs brand">
  <div class="brand-name">U.M.L.</div>
  <div class="brand-tag">UNDER MORNING LANTERN</div>
</div>
<nav class="abs nav">
  <a class="active" href="#" style="left:52px">About</a>
  <a href="#" style="left:97px">Shop</a>
  <a href="#" style="left:148px">Glimmergram</a>
  <a href="#" style="left:246px">Contact</a>
  <a class="track" href="#">Track Order</a>
</nav>
<svg class="abs cart" width="22" height="24" viewBox="0 0 22 24" aria-label="Cart, 0 items">
  <path d="M1 6h3l2.5 9h10l2-6.5H6" fill="none" stroke="#fff" stroke-width="1.3"/>
  <circle cx="8" cy="18.5" r="1.3" fill="none" stroke="#fff" stroke-width="1.2"/>
  <circle cx="15" cy="18.5" r="1.3" fill="none" stroke="#fff" stroke-width="1.2"/>
  <circle cx="17" cy="5" r="5" fill="#111"/>
  <text x="17" y="7.4" text-anchor="middle" font-family="Roboto,sans-serif" font-size="7" fill="#fff">0</text>
</svg>
<h1 class="abs hero-title">ABOUT ME</h1>
<div class="abs crumbs">Home<span>|</span>About Me</div>

<h2 class="abs section-title">ABOUT <em>ME</em></h2>
<div class="abs section-rule"></div>
<div class="abs side-panel" style="left:0"></div>
<div class="abs side-panel" style="left:708px;width:117px"></div>

<div class="abs video">
  <div class="video-frame" role="img" aria-label="Video still: purple and teal label tees hung against a soft floral background"></div>
  <div class="video-caption">About UML Check out the video</div>
  <svg class="play-big" width="45" height="45" viewBox="0 0 45 45" aria-label="Play video">
    <circle cx="22.5" cy="22.5" r="22.5" fill="rgba(120,110,130,.75)"/>
    <path d="M16 12l16 10.5L16 33z" fill="#fff"/>
  </svg>
  <div class="controls">
    <svg style="position:absolute;left:10px;top:10px" width="8" height="9" viewBox="0 0 8 9"><path d="M0 0l7 4.5L0 9z" fill="#fff"/></svg>
    <div class="progress"><i></i></div>
    <span class="time">03:47 / 10:00</span>
    <svg style="position:absolute;left:514px;top:10px" width="11" height="9" viewBox="0 0 11 9"><path d="M0 3h2.5L6 0v9L2.5 6H0z" fill="#fff"/><path d="M8 2.5q1.5 2 0 4M9.5 1q2.5 3.5 0 7" stroke="#fff" fill="none" stroke-width="1"/></svg>
    <span class="hd">HD</span>
  </div>
</div>

<h2 class="abs feed-title">Glimmergram</h2>
<p class="abs feed-text">Meet your fellow Humans! Show us your UML style on Chirper, Glimmergram or Friendbook and tag @UML for a chance to win free tees and be featured on our site!</p>
<div class="tile tile-feature" role="img" aria-label="Purple label tee on a dark slate background"></div>
<div class="tile tile-a" role="img" aria-label="Photo: customer in a graphic tank top against a concrete wall"></div>
<div class="tile tile-b" role="img" aria-label="Photo: customer in a black hoodie in a field"></div>
<div class="tile tile-c" role="img" aria-label="Photo: customer in a white tee by a stone wall"></div>
<div class="tile tile-d" role="img" aria-label="Photo: customer in a hoodie sitting on a deck"></div>

<footer class="abs footer"></footer>
<div class="abs policy">ALL SALES FINAL. NO REFUNDS,<br>RETURNS OR EXCHANGES</div>
<div class="abs policy-rule"></div>
<div class="abs contact-lines">+xxx xxxx xxxxx<br>xxxxxxx@postmail.com</div>
<div class="abs divider" style="left:224px"></div>
<div class="abs col-title" style="left:255px;top:1030px">Contact Us</div>
<div class="abs links">Home<br>About<br>Services<br>Contact</div>
<div class="abs divider" style="left:328px"></div>
<div class="abs col-title" style="left:359px;top:1028px">Email Newsletter</div>
<div class="abs news-note">Sale upto 20 % off for your next purchase inthis month!</div>
<div class="abs subscribe"><span class="field">Email address</span><span class="btn">Subscribe</span></div>
<div class="abs socials"><i></i><i></i><i></i><i></i><i></i></div>
<div class="abs divider" style="left:622px"></div>
<div class="abs brand-foot">
  <div class="brand-name">U.M.L.</div>
  <div class="brand-tag">UNDER MORNING LANTERN</div>
</div>
<div class="abs track-btn">Track Order</div>

<div class="abs footer-bottom"></div>
<div class="abs copyright">© 2020 UML Under Morning Lantern &nbsp;| All Rights Reserved</div>
<div class="abs cards">
  <div class="card">Palo</div>
  <div class="card">Meridian</div>
  <div class="card">Ambercard</div>
  <div class="card">Pennyline</div>
  <div class="card">Dinewell</div>
  <div class="card">Wayfarer</div>
</div>

</body>
</html>
```